Cafe Opening Flyer Design Project

We need a flyer for the grand opening of our new cafe. It should appeal very much to our target consumer - working adults within the CBD area, where there is substantial competition as well.

Keep the message clear to the audience:
(below statements are just examples, please be creative and come up with your own phrases)
1. there's a new cafe you don't wanna miss out..
2. and coffee is always a good idea..

Be bold and creative!
Updates

Dear designers,

Kindly add in our opening hours on the flyer (A5 size, single side)
Weekdays: 7am to 6pm
Sat: 8am to 3pm
Closed on Sun & PH

Thank you!

Target Market(s)

Working adults in the CBD area, coffee lovers

Industry/Entity Type

Cafe

Requirements
Must have
• Location:
48 Penrith Wharf, The Galleria #03-14

```html
<!DOCTYPE html>
<html lang="en">
<head>
<meta charset="utf-8">
<title>Kindly Brewed – A New Cafe</title>
<link href="https://fonts.googleapis.com/css2?family=Permanent+Marker&family=Caveat+Brush&family=Patua+One&family=Patrick+Hand+SC&display=swap" rel="stylesheet">
<style>
  :root {
    --peach-light: #f7dcbc;
    --peach: #efbf8e;
    --peach-deep: #e2a066;
    --cream: #fbe9c8;
    --espresso: #4f2207;
    --mocha: #6b3410;
    --roast: #7a3f12;
    --amber: #f6a300;
    --amber-soft: #f3b35a;
    --white: #ffffff;
    --band: rgba(120, 105, 95, 0.45);
  }
  * { margin: 0; padding: 0; box-sizing: border-box; }
  html, body { width: 927px; height: 1200px; overflow: hidden; background: var(--cream); }
  .flyer {
    position: relative;
    width: 927px;
    height: 1200px;
    overflow: hidden;
    background: radial-gradient(circle at 70% 25%, var(--peach-light) 0%, var(--peach) 55%, var(--peach-deep) 100%);
    font-family: "Patrick Hand SC", cursive;
  }
  .backdrop { position: absolute; inset: 0; }
  .portrait {
    position: absolute;
    left: 0; top: 0;
    width: 560px; height: 790px;
    background: radial-gradient(ellipse at 55% 45%, #d9a07a 0%, #b8774f 45%, #3a2216 100%);
    border-radius: 0 0 120px 0;
    opacity: 0.92;
  }
  .brand {
    position: absolute;
    left: 560px; top: 130px;
    display: flex; align-items: center; gap: 14px;
  }
  .brand-dot { width: 24px; height: 24px; border-radius: 50%; background: var(--roast); }
  .brand-name { font-size: 60px; color: var(--roast); line-height: 1; }
  .band {
    position: absolute;
    left: 0; top: 373px;
    width: 927px; height: 163px;
    background: var(--band);
  }
  .headline {
    position: absolute;
    left: 0; top: 385px;
    width: 927px;
    text-align: center;
    font-family: "Permanent Marker", "Caveat Brush", cursive;
    font-weight: 400;
    font-size: 116px;
    line-height: 1.1;
    color: var(--roast);
    letter-spacing: 2px;
    text-shadow: 0 0 3px var(--white), 0 0 3px var(--white), 0 0 6px var(--white);
  }
  .tagline {
    position: absolute;
    left: 30px; top: 610px;
    width: 880px;
    text-align: center;
    font-family: "Patua One", serif;
    font-variant: small-caps;
    font-size: 80px;
    line-height: 1;
    color: var(--amber);
    transform: rotate(-8deg);
    -webkit-text-stroke: 2px var(--mocha);
    text-shadow: 3px 3px 0 var(--mocha);
  }
  .hours {
    position: absolute;
    right: 36px; top: 752px;
    text-align: right;
    font-size: 26px;
    line-height: 1.15;
    color: var(--mocha);
  }
  .hours-title { font-size: 28px; color: var(--roast); }
  .base { position: absolute; inset: 0; }
  .location-label {
    position: absolute;
    left: 286px; top: 836px;
    font-size: 42px;
    color: var(--amber-soft);
  }
  .address {
    position: absolute;
    left: 36px; top: 896px;
    font-size: 47px;
    color: var(--amber-soft);
    letter-spacing: 1px;
    white-space: nowrap;
  }
  .slogan {
    position: absolute;
    left: 0; width: 927px;
    text-align: center;
    font-family: "Patrick Hand SC", cursive;
    font-size: 84px;
    color: var(--white);
    text-shadow: 3px 3px 0 #1e0c02;
    line-height: 1;
    white-space: nowrap;
  }
  .slogan-first { top: 982px; }
  .slogan-second { top: 1086px; padding-left: 40px; }
</style>
</head>
<body>
<main class="flyer">
  <svg class="backdrop" width="927" height="1200" viewBox="0 0 927 1200" aria-hidden="true">
    <circle cx="700" cy="250" r="330" fill="#f5d2ac" opacity="0.55"/>
    <circle cx="460" cy="300" r="470" fill="none" stroke="#f6d9b6" stroke-width="30" opacity="0.5"/>
    <g fill="#f6d3ad" opacity="0.7">
      <rect x="560" y="885" width="367" height="10"/>
      <rect x="560" y="910" width="367" height="10"/>
      <rect x="560" y="935" width="367" height="10"/>
    </g>
  </svg>

  <div class="portrait" role="img" aria-label="Photo of a man at a table sipping from a cafe mug"></div>

  <div class="brand">
    <span class="brand-dot"></span>
    <span class="brand-name">Kindly Brewed</span>
  </div>

  <div class="band"></div>
  <h1 class="headline">A NEW CAFE</h1>
  <p class="tagline">Good to the Last Drop!</p>

  <svg class="base" width="927" height="1200" viewBox="0 0 927 1200" aria-hidden="true">
    <path d="M0 800 Q 380 700 720 880 Q 900 990 880 1200 L0 1200 Z" fill="var(--espresso)"/>
  </svg>

  <div class="hours">
    <p class="hours-title">Opening Hours</p>
    <p>Weekdays: 7am – 6pm</p>
    <p>Sat: 8am – 3pm</p>
    <p>Closed on Sun &amp; PH</p>
  </div>

  <p class="location-label">Location:</p>
  <p class="address">48 Penrith Wharf, The Galleria #03-14</p>
  <p class="slogan slogan-first">DO STUPID THINGS FASTER</p>
  <p class="slogan slogan-second">WITH MORE ENERGY</p>
</main>
</body>
</html>
```